Cover for Lanterns Along the Quiet Shore of Being

Cover for a book that describes everything that happens to a person, from pre-birth life plans through growing in compassion and wisdom to death and living in the afterlife. The information is revealed in messages from people living in the life after this life. The title is Lessons Gathered From Every Season of Your Existence: Shared by Voices Dwelling Beyond the Veil. Author is T. Wesley Prandt. Book size is 6 by 9.

Target Market(s)

General

Font styles to use
Serif

```html
<!DOCTYPE html>
<html lang="en">
<head>
<meta charset="utf-8">
<title>Lanterns Along the Quiet Shore of Being — Book Cover</title>
<link href="https://fonts.googleapis.com/css2?family=Marcellus&family=Lato:wght@400;700;900&display=swap" rel="stylesheet">
<style>
  :root {
    --page-bg: #ffffff;
    --sky-dark: #1b201d;
    --sky-mid: #4a524c;
    --haze: #9ea08f;
    --glow: #f2c77a;
    --glow-soft: #e9d9b4;
    --water-light: #eef2f1;
    --water-pale: #d9e3e6;
    --title-ink: #f1ebdf;
    --body-ink: #15181a;
    --rule: #8d959a;
  }
  * { margin: 0; padding: 0; box-sizing: border-box; }
  html, body {
    width: 1200px;
    height: 1000px;
    overflow: hidden;
    background: var(--page-bg);
  }
  .canvas {
    position: relative;
    width: 1200px;
    height: 1000px;
  }
  .cover {
    position: absolute;
    left: 291px;
    top: 33px;
    width: 619px;
    height: 929px;
    overflow: hidden;
  }
  .cover-photo {
    position: absolute;
    inset: 0;
    background:
      radial-gradient(ellipse 140px 90px at 62% 61%, rgba(255,236,190,0.95), rgba(242,199,122,0.55) 45%, rgba(242,199,122,0) 100%),
      radial-gradient(ellipse 420px 160px at 55% 62%, rgba(233,217,180,0.55), rgba(233,217,180,0) 100%),
      linear-gradient(to bottom,
        var(--sky-dark) 0%,
        #262c28 18%,
        var(--sky-mid) 36%,
        #6c6f62 48%,
        var(--haze) 56%,
        #c9b98f 61%,
        #d8d2bf 66%,
        var(--water-light) 78%,
        var(--water-pale) 100%);
  }
  .title-block {
    position: absolute;
    top: 72px;
    left: 0;
    width: 100%;
    text-align: center;
    color: var(--title-ink);
    font-family: "Marcellus", serif;
  }
  .title-lead {
    font-size: 22px;
    letter-spacing: 0.5px;
    line-height: 1;
  }
  .title-main {
    margin-top: 14px;
    font-size: 68px;
    line-height: 74px;
    letter-spacing: 0.5px;
  }
  .subtitle {
    position: absolute;
    top: 786px;
    left: 0;
    width: 100%;
    text-align: center;
    font-family: "Lato", sans-serif;
    font-weight: 700;
    font-size: 17px;
    color: var(--body-ink);
  }
  .divider {
    position: absolute;
    top: 827px;
    left: 70px;
    width: 475px;
    height: 1px;
    background: var(--rule);
  }
  .author {
    position: absolute;
    top: 860px;
    left: 0;
    width: 100%;
    text-align: center;
    font-family: "Lato", sans-serif;
    font-weight: 900;
    font-size: 21px;
    letter-spacing: 4px;
    color: var(--body-ink);
  }
</style>
</head>
<body>
  <main class="canvas">
    <section class="cover">
      <div class="cover-photo" role="img" aria-label="Photograph of a figure walking along a rocky shoreline at sunset, reflected upside down in still water, with dark stones floating in a dusky sky"></div>
      <h1 class="title-block">
        <span class="title-lead" style="display:block">LESSONS GATHERED FROM EVERY</span>
        <span class="title-main" style="display:block">SEASON OF<br>YOUR<br>EXISTENCE</span>
      </h1>
      <p class="subtitle">Shared by Voices Dwelling Beyond the Veil.</p>
      <div class="divider"></div>
      <p class="author">T. WESLEY PRANDT</p>
    </section>
  </main>
</body>
</html>
```